Walk Beside The River

Business Card design

Target Market(s)

People who require support in the commnity

Industry/Entity Type

Mental Health Support

Contact Information for Business Card

Mental Health Support Rosalind Tavener walkbesidetheriver@mailcove.com.au 0481 637 092 PO Box 926 Tallowmere WRN 5812

Colors
6B429C
8869AF
B7A5CE
E3DAEB
F3F0F8

Requirements
Must have
• Logo & details listed above
Should not have
• No red or orange

```html
<!DOCTYPE html>
<html lang="en">
<head>
<meta charset="utf-8">
<title>Walk Beside The River — Business Card</title>
<link rel="stylesheet" href="https://fonts.googleapis.com/css2?family=Open+Sans:wght@400;700&display=swap">
<style>
  :root {
    --backdrop: #2b2b30;
    --card: #1f1e24;
    --purple: #6b429c;
    --purple-soft: #8869af;
    --lilac: #e3daeb;
    --yellow: #ece526;
    --text: #f3f0f8;
    --emboss: #18171c;
  }
  * { margin: 0; padding: 0; box-sizing: border-box; }
  html, body {
    width: 1200px; height: 780px; overflow: hidden;
    background: var(--backdrop);
    font-family: "Open Sans", Arial, sans-serif;
    color: var(--text);
  }
  .canvas {
    position: relative; width: 1200px; height: 780px;
    display: flex; align-items: center; justify-content: center; gap: 60px;
  }
  .card {
    position: relative; width: 520px; height: 300px;
    background: var(--card); border-radius: 4px; overflow: hidden;
    box-shadow: 0 10px 30px rgba(0,0,0,.45);
  }
  .brand-mark {
    position: absolute; border-radius: 50%;
    background: var(--purple);
    display: flex; align-items: center; justify-content: center; text-align: center;
  }
  .brand-mark__name {
    font-weight: 700; color: var(--text); text-transform: uppercase;
    letter-spacing: .12em; line-height: 1.35;
  }
  .card--front .brand-mark { left: 34px; top: 22px; width: 112px; height: 112px; }
  .card--front .brand-mark__name { font-size: 11px; }
  .details {
    position: absolute; left: 34px; top: 148px; font-size: 12.5px; line-height: 1.55;
  }
  .details__service, .details__contact-name { padding-left: 2px; }
  .details__line { display: flex; align-items: center; gap: 7px; }
  .details__icon { width: 12px; height: 12px; flex: none; fill: var(--yellow); }
  .holder {
    position: absolute; right: 40px; top: 108px; text-align: right;
  }
  .holder__name { font-size: 27px; font-weight: 700; line-height: 1.1; }
  .holder__first { color: var(--yellow); }
  .holder__last { color: var(--purple-soft); }
  .holder__role { font-size: 13px; margin-top: 4px; }
  .edge-tab {
    position: absolute; right: 0; top: 168px; width: 14px; height: 56px;
    background: var(--yellow);
  }
  .faint-name {
    position: absolute; right: 40px; bottom: 14px;
    font-size: 15px; font-weight: 700; color: var(--emboss);
    text-transform: uppercase; letter-spacing: .12em;
  }
  .card--back .brand-mark {
    left: 50%; top: 50%; width: 190px; height: 190px; transform: translate(-50%, -50%);
  }
  .card--back .brand-mark__name { font-size: 16px; }
</style>
</head>
<body>
<main class="canvas">
  <section class="card card--front" aria-label="Business card front">
    <div class="brand-mark"><span class="brand-mark__name">Walk Beside<br>The River</span></div>
    <div class="details">
      <p class="details__service">Mental Health Support</p>
      <p class="details__contact-name">Rosalind Tavener</p>
      <p class="details__line">
        <svg class="details__icon" viewBox="0 0 24 24" aria-hidden="true"><path d="M6.6 10.8a15.1 15.1 0 0 0 6.6 6.6l2.2-2.2a1 1 0 0 1 1-.25 11.4 11.4 0 0 0 3.6.57 1 1 0 0 1 1 1V20a1 1 0 0 1-1 1A17 17 0 0 1 3 4a1 1 0 0 1 1-1h3.5a1 1 0 0 1 1 1c0 1.250.2 2.45.57 3.57a1 1 0 0 1-.25 1z"/></svg>
        <span>0481 637 092</span>
      </p>
      <p class="details__line">
        <svg class="details__icon" viewBox="0 0 24 24" aria-hidden="true"><path d="M2 5h20v14H2zm2 2v.5l8 5 8-5V7zm0 2.9V17h16V9.9l-8 5z"/></svg>
        <span>walkbesidetheriver@mailcove.com.au</span>
      </p>
      <p class="details__line">
        <svg class="details__icon" viewBox="0 0 24 24" aria-hidden="true"><path d="M12 2a7 7 0 0 0-7 7c0 5.2 7 13 7 13s7-7.8 7-13a7 7 0 0 0-7-7zm0 9.5A2.5 2.5 0 1 1 12 6.5a2.5 2.5 0 0 1 0 5z"/></svg>
        <span>PO Box 926 Tallowmere WRN 5812</span>
      </p>
    </div>
    <div class="holder">
      <p class="holder__name"><span class="holder__first">Ilona</span> <span class="holder__last">Marsdale</span></p>
      <p class="holder__role">CEO/Director</p>
    </div>
    <div class="edge-tab"></div>
    <p class="faint-name" aria-hidden="true">Walk Beside The River</p>
  </section>

  <section class="card card--back" aria-label="Business card back">
    <div class="brand-mark"><span class="brand-mark__name">Walk Beside<br>The River</span></div>
  </section>
</main>
</body>
</html>
```